Striking new Advert required for Commercial Real Estate Agency

We need a a NEW newspaper advertisement for the marketing of a large commercial property (a Backpackers lodge)

Dimensions are to be width of 101mm and height of 100mm (10cms)

Our key design statement for this advert is clean, modern and minimalist design, with accents of 'HOT PINK' colour to remove it from looking too boring, perhaps in the area of the contact icons. The heirachy of the advert is outlined in the attached ADVERTISEMENT TEXT FILE.

Our company name is THE HARBOURLINE COLLECTIVE, and we want our brand to appear professional yet classy in it's design style (sort of like an advertising or design agency)

We have two logo options below, one more square in its layout (which we prefer) and the other more rectangular, which may be better suited for the layout. We are not adverse to the logo being reversed (white text on black), along with other key element areas such as the main advert heading and the "FOR SALE" part, and think this would be a good option.
There are two photos attached to be included in the advert.

We have attached an example of an old advert that we did, which we DID NOT LIKE, and which was for a smaller width than the one we need (it is only 65% of the width of this one). WE have also atached a file showing layout of some of our competitors adverts, which we dont think are too good either.

We are really open for ideas, but have time pressures, so please come back with any questions as soon as you can, if needed.

Thank you
Updates

Thank you for the great and diverse designs. There are a few standout options, but one style that we prefer most.

Target Market(s)

We are wanting this newspaper advertisement to attract interest from real estat e developers, investors and motel/lodge owners, along with other high nett worth individuals

Industry/Entity Type

Real Estate

Font styles to use
Serif
Sans Serif

Colors
1b1b1b
a54499
474747
fbfbfb

Requirements
Must have
• Clean modern look, predominantly monochromatic or black and white, with the hot pink accent somewhere, as mentioned above.
• All the contents of the TEXT provided, perhaps with additional space to add a little more if needed, Please advise if you think we dont have enough space for all of the TEXT
Should not have
• Script like fonts
• Cartoonish characters
• a 'cheap' look

```html
<!DOCTYPE html>
<html lang="en">
<head>
<meta charset="utf-8">
<title>For Sale – Mount Victoria Land Grab</title>
<link href="https://fonts.googleapis.com/css2?family=Montserrat:wght@500;600;700&family=Roboto+Condensed:wght@300;400;700&display=swap" rel="stylesheet">
<style>
  :root {
    --hot-pink: #a8248f;
    --ink: #1b1b1b;
    --panel: #231f20;
    --paper: #ffffff;
    --backdrop: #e4e4e4;
    --white: #fbfbfb;
  }
  * { margin: 0; padding: 0; box-sizing: border-box; }
  html, body { width: 1200px; height: 1000px; overflow: hidden; }
  body { background: var(--backdrop); position: relative; font-family: "Roboto Condensed", Arial, sans-serif; color: var(--ink); }

  .advert { position: absolute; left: 158px; top: 68px; width: 885px; height: 876px; background: var(--paper); }

  .headline { position: absolute; left: 31px; top: 25px; font-family: "Montserrat", Arial, sans-serif; font-weight: 700; font-size: 66px; line-height: 1; letter-spacing: 0.5px; color: var(--hot-pink); }

  .listing-title { position: absolute; right: 26px; top: 47px; text-align: right; font-family: "Montserrat", Arial, sans-serif; color: var(--ink); }
  .listing-title .name { font-weight: 600; font-size: 19px; line-height: 22px; }
  .listing-title .address { font-weight: 600; font-size: 14.5px; line-height: 22px; }

  .photo { position: absolute; top: 113px; height: 368px; }
  .photo-aerial { left: 0; width: 513px; background: linear-gradient(160deg, #9fb5a0 0%, #c9c6bd 35%, #8e8f8c 60%, #6f7d4a 100%); }
  .photo-facade { left: 519px; width: 366px; background: linear-gradient(180deg, #4f86cc 0%, #9cbde0 25%, #e9e9ec 45%, #d2d3d6 70%, #5f7a3c 100%); }

  .description { position: absolute; left: 27px; top: 507px; width: 528px; font-size: 21.5px; line-height: 29.5px; font-weight: 400; color: var(--ink); }
  .features { list-style: none; }
  .features li { position: relative; padding-left: 18px; }
  .features li::before { content: ""; position: absolute; left: 1px; top: 11px; width: 9px; height: 9px; background: var(--hot-pink); }

  .contact-panel { position: absolute; left: 569px; top: 489px; width: 316px; height: 387px; background: var(--panel); color: var(--white); }
  .tender { position: absolute; left: 19px; top: 20px; font-weight: 700; font-size: 21px; }

  .brand-name { position: absolute; left: 19px; top: 80px; width: 280px; font-family: "Roboto Condensed", Arial, sans-serif; font-weight: 700; font-size: 30px; line-height: 34px; color: var(--white); }

  .agent { position: absolute; left: 19px; top: 186px; font-weight: 700; font-size: 19.5px; line-height: 27px; }
  .contact-list { position: absolute; left: 15px; top: 240px; list-style: none; font-weight: 700; font-size: 19.5px; line-height: 27.5px; }
  .contact-list li { display: flex; align-items: center; gap: 6px; }
  .contact-list svg { width: 18px; height: 18px; flex: none; }
</style>
</head>
<body>
  <div class="advert">
    <h1 class="headline">FOR SALE</h1>
    <div class="listing-title">
      <div class="name">MOUNT VICTORIA LAND GRAB</div>
      <div class="address">Linden’s Lodge, 82 Calder Street, Mount Victoria</div>
    </div>

    <div class="photo photo-aerial" role="img" aria-label="Aerial photo of the lodge buildings, car park and surrounding hillside suburb"></div>
    <div class="photo photo-facade" role="img" aria-label="Photo of the white weatherboard lodge facade with balconies under blue sky"></div>

    <div class="description">
      <p>This Old Beauty has served many, and is now ripe for development.</p>
      <p>One of Mt Vic’s largest land areas, now offered with vacant possession, with key details being:</p>
      <ul class="features">
        <li>Large Land area of 2076m² with elevated sunny position and great outlook + access from Hanlon Street</li>
        <li>Existing Backpackers Lodge of 970m² providing multiple rooms with amenity areas</li>
        <li>Four adjacent sites also available, taking total land area to 4452m², an unprecedented Land</li>
        <li>Offering in this popular cuity fringe location</li>
      </ul>
    </div>

    <div class="contact-panel">
      <div class="tender">Now Selling by Closed Tender</div>
      <div class="brand-name">The Harbourline Collective</div>
      <div class="agent">Contact the Sole Agenct :<br>Mark Tolland</div>
      <ul class="contact-list">
        <li><svg viewBox="0 0 24 24"><path fill="var(--hot-pink)" d="M6.6 10.8a15.1 15.1 0 0 0 6.6 6.6l2.2-2.2a1 1 0 0 1 1-.25 11.4 11.4 0 0 0 3.6.57 1 1 0 0 1 1 1V20a1 1 0 0 1-1 1A17 17 0 0 1 3 4a1 1 0 0 1 1-1h3.5a1 1 0 0 1 1 1c0 1.25.2 2.45.57 3.57a1 1 0 0 1-.25 1z"/></svg>(04) 555 0142</li>
        <li><svg viewBox="0 0 24 24"><rect x="7" y="2" width="10" height="20" rx="2" fill="none" stroke="var(--hot-pink)" stroke-width="2.2"/><circle cx="12" cy="18" r="1.3" fill="var(--hot-pink)"/></svg>(021) 555 781</li>
        <li><svg viewBox="0 0 24 24"><rect x="2" y="5" width="20" height="14" rx="1" fill="var(--hot-pink)"/><path d="M2 6l10 7 10-7" fill="none" stroke="var(--panel)" stroke-width="1.8"/></svg>mark@harbourline.co.nz</li>
        <li><svg viewBox="0 0 24 24"><g fill="none" stroke="var(--hot-pink)" stroke-width="2"><circle cx="12" cy="12" r="9.5"/><ellipse cx="12" cy="12" rx="4" ry="9.5"/><path d="M2.5 12h19M4 7h16M4 17h16"/></g></svg>www.harbourline.co.nz</li>
      </ul>
    </div>
  </div>
</body>
</html>
```